Website Design Request - Management Consulting Firm

We need a Website designed for an IT Management Staffing and Recruiting firm called TRAVENOK based in San Francisco.

The firm is an high-end technology staffing agency. Our focus is on quality and high-caliber candidates rather than quantity.

The website will have two main home pages. One for the recruiter and another on for the candidates.

The website needs to optimize for mobile devices as well.

I have attached few mock-ups that I have done just to show what I am thinking. The UI needs to be very clean, fluid, and it needs to have a modern, rustic, professional feel to it.

Target Market(s)

Technology Manager, Director, VP, CIO of Companies that have $4b-10b dollar revenue. Such as larkspurdwellings.example , https://www.velmorian.example/, quillnet.example, zib.example

Industry/Entity Type

Management Consulting

Number of Pages Required

5+ page

Font styles to use
Sans Serif

Colors
f37122
ffffff

Requirements
Must have
• Please review mock-ups for suggestions
Nice to have
Should not have

```html
<!DOCTYPE html>
<html lang="en">
<head>
<meta charset="utf-8">
<title>TRAVENOK — IT Project Management Jobs</title>
<link rel="stylesheet" href="https://fonts.googleapis.com/css2?family=Mulish:wght@400;600;700;800&display=swap">
<style>
  :root {
    --orange: #f37122;
    --orange-dark: #e0601a;
    --white: #ffffff;
    --ink: #555555;
    --ink-soft: #7a7a7a;
    --panel: #f5f6f8;
    --tab-dark: #454545;
    --footer: #2b2b2b;
    --footer-line: #444444;
    --footer-text: #d6d6d6;
  }
  * { box-sizing: border-box; margin: 0; padding: 0; }
  html, body { width: 1043px; height: 1200px; overflow: hidden; }
  body { position: relative; font-family: "Mulish", Arial, sans-serif; background: var(--white); color: var(--ink); }

  .site-header { position: absolute; left: 0; top: 0; width: 1043px; height: 78px; background: var(--white); border-bottom: 1px solid #d8d8d8; }
  .brand { position: absolute; left: 75px; top: 24px; display: flex; align-items: center; gap: 8px; font-size: 30px; font-weight: 800; color: var(--orange); letter-spacing: 1px; line-height: 1; }
  .brand-dot { width: 12px; height: 12px; border-radius: 50%; background: var(--orange); }
  .main-nav a { position: absolute; top: 36px; font-size: 10.5px; font-weight: 600; color: #555; text-decoration: none; letter-spacing: .3px; }

  .hero { position: absolute; left: 0; top: 79px; width: 1043px; height: 412px; background: radial-gradient(ellipse at 60% 55%, #5b5048 0%, #3b302a 45%, #231c18 100%); color: var(--white); text-align: center; }
  .hero-title { position: absolute; left: 0; right: 0; top: 138px; font-size: 22px; font-weight: 800; letter-spacing: .3px; }
  .hero-sub { position: absolute; left: 0; right: 0; top: 180px; font-size: 16px; font-weight: 400; }
  .offer-form { position: absolute; left: 246px; top: 235px; width: 552px; height: 44px; display: flex; border: 1px solid var(--white); border-radius: 3px; overflow: hidden; }
  .offer-field { flex: 1; background: var(--white); padding-left: 19px; font-size: 12.5px; color: #555; display: flex; align-items: center; }
  .offer-button { width: 135px; background: var(--orange); color: var(--white); font-size: 12.5px; font-weight: 800; display: flex; align-items: center; justify-content: center; }
  .hero-note { position: absolute; left: 0; right: 0; top: 292px; font-size: 11px; }
  .hero-note span { text-decoration: underline; }
  .slide-arrow { position: absolute; top: 184px; width: 46px; height: 46px; }

  .tabs { position: absolute; left: 0; top: 491px; width: 1043px; height: 49px; display: flex; }
  .tab { display: flex; align-items: center; justify-content: center; font-size: 18px; font-weight: 800; color: var(--white); }
  .tab-active { width: 521px; background: var(--orange); position: relative; }
  .tab-active::after { content: ""; position: absolute; left: 253px; bottom: -7px; border-left: 7px solid transparent; border-right: 7px solid transparent; border-top: 7px solid var(--orange); }
  .tab-other { flex: 1; background: var(--tab-dark); }

  .how-it-works { position: absolute; left: 0; top: 540px; width: 1043px; height: 456px; background: var(--panel); }
  .product-visual { position: absolute; left: 75px; top: 66px; width: 305px; height: 294px; background: linear-gradient(160deg, #e9e9ea 0%, #cfd0d2 100%); border-radius: 6px; }
  .section-title { position: absolute; left: 438px; top: 58px; font-size: 17px; font-weight: 700; color: #5a5a5a; }
  .step { position: absolute; left: 438px; width: 560px; height: 50px; }
  .step-icon { position: absolute; left: 2px; top: 0; width: 47px; height: 47px; }
  .step-title { position: absolute; left: 66px; top: 0; font-size: 12px; font-weight: 600; color: #444; }
  .step-text { position: absolute; left: 66px; top: 21px; font-size: 10.5px; color: var(--ink-soft); white-space: nowrap; }
  .upload-button { position: absolute; left: 438px; top: 379px; width: 204px; height: 38px; background: var(--orange); border-radius: 2px; color: var(--white); font-size: 11.5px; font-weight: 800; display: flex; align-items: center; justify-content: center; gap: 9px; }

  .site-footer { position: absolute; left: 0; top: 996px; width: 1043px; height: 204px; background: var(--footer); }
  .social { position: absolute; top: 28px; width: 52px; height: 52px; border: 1px solid #cfcfcf; border-radius: 50%; display: flex; align-items: center; justify-content: center; }
  .footer-rule { position: absolute; left: 75px; top: 92px; width: 893px; height: 1px; background: var(--footer-line); }
  .footer-nav { position: absolute; left: 0; right: 0; top: 114px; text-align: center; font-size: 10.5px; color: var(--footer-text); }
  .footer-nav span { margin: 0 18px; }
  .copyright { position: absolute; left: 0; right: 0; top: 152px; text-align: center; font-size: 10px; color: var(--footer-text); }
  .footer-strip { position: absolute; left: 0; bottom: 0; width: 1043px; height: 2px; background: var(--orange); }
</style>
</head>
<body>
  <header class="site-header">
    <div class="brand"><span class="brand-dot"></span>TRAVENOK</div>
    <nav class="main-nav">
      <a style="left:637px">PROFESSIONALS</a>
      <a style="left:757px">EMPLOYERS</a>
      <a style="left:854px">SIGN IN</a>
      <a style="left:928px">SIGN UP</a>
    </nav>
  </header>

  <section class="hero" role="img" aria-label="Photo of a person typing on a laptop showing a job search page">
    <svg class="slide-arrow" style="left:23px" viewBox="0 0 46 46"><circle cx="23" cy="23" r="22" fill="none" stroke="#fff" stroke-width="1.5"/><path d="M26 15 L18 23 L26 31" fill="none" stroke="#fff" stroke-width="3"/></svg>
    <svg class="slide-arrow" style="left:975px" viewBox="0 0 46 46"><circle cx="23" cy="23" r="22" fill="none" stroke="#fff" stroke-width="1.5"/><path d="M20 15 L28 23 L20 31" fill="none" stroke="#fff" stroke-width="3"/></svg>
    <h1 class="hero-title">LOOKING FOR IT PROJECT MANAGMENT JOBS?</h1>
    <p class="hero-sub">Upload your Resume accept interview requests get offers</p>
    <div class="offer-form">
      <div class="offer-field">Your Email Address :</div>
      <div class="offer-button">GET OFFERS NOW</div>
    </div>
    <p class="hero-note">Looking for talents? <span>See how it works for Employers</span></p>
  </section>

  <div class="tabs">
    <div class="tab tab-active">HOW IT WORKS?</div>
    <div class="tab tab-other">WHY US?</div>
  </div>

  <section class="how-it-works">
    <div class="product-visual" role="img" aria-label="Desktop computer with keyboard and mouse displaying the firm name"></div>
    <h2 class="section-title">Employers pay 25% more for a better FIT project Manager</h2>

    <div class="step" style="top:122px">
      <svg class="step-icon" viewBox="0 0 47 47"><circle cx="23.5" cy="23.5" r="22.5" fill="none" stroke="var(--orange)" stroke-width="1.5"/><rect x="15" y="13" width="15" height="20" fill="none" stroke="var(--orange)" stroke-width="1.5"/><path d="M18 18h9M18 22h9M18 26h6" stroke="var(--orange)" stroke-width="1.5"/><path d="M27 32 L34 25" stroke="var(--orange)" stroke-width="2"/></svg>
      <div class="step-title">UPLOAD YOUR RESUME</div>
      <div class="step-text">Answer few questions and upload your resume.</div>
    </div>
    <div class="step" style="top:205px">
      <svg class="step-icon" viewBox="0 0 47 47"><circle cx="23.5" cy="23.5" r="22.5" fill="none" stroke="var(--orange)" stroke-width="1.5"/><rect x="17" y="11" width="13" height="8" rx="3" fill="var(--orange)"/><circle cx="15" cy="24" r="3" fill="var(--orange)"/><circle cx="32" cy="24" r="3" fill="var(--orange)"/><path d="M11 34 v-4 h8 v4 M28 34 v-4 h8 v4 M19 30 h9" stroke="var(--orange)" stroke-width="1.8" fill="none"/></svg>
      <div class="step-title">WE SEND YOU INTERVIEW REQUESTS</div>
      <div class="step-text">Interested in someone? With a single click, send interview request and let us handle the rest.</div>
    </div>
    <div class="step" style="top:291px">
      <svg class="step-icon" viewBox="0 0 47 47"><circle cx="23.5" cy="23.5" r="22.5" fill="none" stroke="var(--orange)" stroke-width="1.5"/><circle cx="23.5" cy="23.5" r="13" fill="var(--orange)"/><rect x="22" y="15" width="3" height="11" fill="#fff"/><circle cx="23.5" cy="30" r="1.8" fill="#fff"/></svg>
      <div class="step-title">GET $1000 BONUS</div>
      <div class="step-text">Find a job and get $1000 bonus TRAVENOK</div>
    </div>

    <div class="upload-button">
      <svg width="14" height="13" viewBox="0 0 14 13"><path d="M7 0v7M3.5 4 L7 7.5 L10.5 4" stroke="#fff" stroke-width="2" fill="none"/><path d="M1 9v3h12V9" stroke="#fff" stroke-width="2" fill="none"/></svg>
      UPLOAD YOUR RESUME
    </div>
  </section>

  <footer class="site-footer">
    <span class="social" style="left:340px" aria-label="Social profile"></span>
    <span class="social" style="left:403px" aria-label="Social profile"></span>
    <span class="social" style="left:464px" aria-label="Social profile"></span>
    <span class="social" style="left:527px" aria-label="Social profile"></span>
    <span class="social" style="left:588px" aria-label="Social profile"></span>
    <span class="social" style="left:652px" aria-label="Email">
      <svg width="16" height="12" viewBox="0 0 16 12"><rect x="1" y="1" width="14" height="10" fill="none" stroke="#fff" stroke-width="1.5"/><path d="M1 1 L8 7 L15 1" fill="none" stroke="#fff" stroke-width="1.5"/></svg>
    </span>
    <div class="footer-rule"></div>
    <nav class="footer-nav">
      <span>PROFESSIONALS</span>|<span>EMPLOYERS</span>|<span>SIGN IN</span>|<span>SIGN UP</span>
    </nav>
    <p class="copyright">© Copyrights 2016 .Travenok Tech.All Rights Reserved.</p>
    <div class="footer-strip"></div>
  </footer>
</body>
</html>
```